Kelvara Pane Works Business Card

We need a business card design that is suitable for a Glazing Business. We Specialize in Repairing broken windows and doors and are a 24hr on call service. We manufacture Shower screens, Fly screens, Wardrobe doors, Security doors and grilles + mirrors. We stock a variety of mesh including Standard mesh, Pet resistant mesh, Tressmet & Clearweft. We would like to use a combination of Light Blue, Dark Blue, Black & White with perhaps a picture of glass breaking.

Industry/Entity Type

Business

Contact Information for Business Card

Narooma Glass Service60B Glasshouse Rocks RdNarooma NSW 2546PH / FAX - 02 44765210MOB - 0419682350 Andrewemail - kelvarapane@fenmail.example

Font styles to use
Serif

Colors
34a7d8
0255a3
ffffff

Requirements
Must have
• logo with picture of broken or cracked glass

```html
<!DOCTYPE html>
<html lang="en">
<head>
<meta charset="utf-8">
<title>Kelvara Pane Works – Business Card</title>
<link rel="stylesheet" href="https://fonts.googleapis.com/css2?family=Cormorant+Garamond:wght@500&family=Exo+2:wght@300&display=swap">
<style>
  :root {
    --stage: #e4e0da;
    --card-black: #07080c;
    --light-blue: #8fc4e0;
    --white: #f4f6fa;
  }
  html, body {
    margin: 0;
    width: 1200px;
    height: 1023px;
    overflow: hidden;
    background: var(--stage);
  }
  .canvas {
    position: relative;
    width: 1200px;
    height: 1023px;
    display: flex;
    align-items: center;
    justify-content: center;
  }
  .card {
    position: relative;
    width: 1000px;
    height: 571px;
    background: radial-gradient(ellipse at 30% 55%, #1a1d26 0%, var(--card-black) 70%);
    border-radius: 6px;
    overflow: hidden;
    box-shadow: 0 10px 30px rgba(0,0,0,.25);
  }
  .card__strips {
    position: absolute;
    inset: 0;
    width: 100%;
    height: 100%;
  }
  .brand {
    position: absolute;
    left: 70px;
    top: 215px;
    display: flex;
    align-items: center;
    gap: 18px;
  }
  .brand__mark {
    width: 46px;
    height: 46px;
    border-radius: 50%;
    background: var(--white);
    flex: none;
  }
  .brand__name {
    font-family: "Cormorant Garamond", serif;
    font-weight: 500;
    font-size: 64px;
    line-height: 0.95;
    color: var(--light-blue);
    margin: 0;
  }
  .brand__line { display: block; white-space: nowrap; }
  .contact {
    position: absolute;
    right: 60px;
    top: 60px;
    margin: 0;
    padding: 0;
    list-style: none;
    font-family: "Exo 2", sans-serif;
    font-weight: 300;
    font-size: 22px;
    line-height: 38px;
    color: var(--white);
  }
  .contact__item {
    display: flex;
    align-items: center;
    gap: 16px;
  }
  .contact__icon {
    width: 18px;
    height: 18px;
    flex: none;
    fill: var(--white);
  }
</style>
</head>
<body>
<main class="canvas">
  <section class="card" aria-label="Kelvara Pane Works business card">
    <svg class="card__strips" viewBox="0 0 1000 571" role="img" aria-label="Slanted glass strips filled with deep blue starry nebula imagery over cracked black glass">
      <defs>
        <linearGradient id="nebula" x1="0" y1="0" x2="1" y2="1">
          <stop offset="0" stop-color="#2a3470"/>
          <stop offset=".5" stop-color="#5b6cc0"/>
          <stop offset="1" stop-color="#1e2658"/>
        </linearGradient>
      </defs>
      <g fill="url(#nebula)" opacity=".92">
        <polygon points="420,571 470,571 700,0 650,0"/>
        <polygon points="490,571 545,571 775,0 720,0"/>
        <polygon points="565,571 615,571 845,0 795,0"/>
        <polygon points="635,571 680,571 910,0 865,0"/>
        <polygon points="700,571 740,571 970,0 930,0"/>
        <polygon points="0,80 90,0 150,0 0,130"/>
        <polygon points="0,520 120,430 170,430 50,520"/>
        <polygon points="860,571 1000,440 1000,500 920,571"/>
      </g>
      <rect x="585" y="40" width="395" height="230" rx="4" fill="var(--card-black)" opacity=".88"/>
    </svg>

    <div class="brand">
      <span class="brand__mark" aria-hidden="true"></span>
      <h1 class="brand__name"><span class="brand__line">Kelvara</span><span class="brand__line">Pane Works</span></h1>
    </div>

    <ul class="contact">
      <li class="contact__item">
        <svg class="contact__icon" viewBox="0 0 24 24" aria-hidden="true"><rect x="6" y="1" width="12" height="22" rx="2"/><rect x="8" y="4" width="8" height="13" fill="#07080c"/></svg>
        0419682350
      </li>
      <li class="contact__item">
        <svg class="contact__icon" viewBox="0 0 24 24" aria-hidden="true"><path d="M6 2l4 4-2 3c1.5 3 4 5.5 7 7l3-2 4 4-3 4C10 21 3 14 2 5z"/></svg>
        02 48931067
      </li>
      <li class="contact__item">
        <svg class="contact__icon" viewBox="0 0 24 24" aria-hidden="true"><path d="M2 5h20v14H2z"/><path d="M2 5l10 8 10-8" fill="none" stroke="#07080c" stroke-width="2"/></svg>
        kelvarapane@fenmail.example
      </li>
      <li class="contact__item">
        <svg class="contact__icon" viewBox="0 0 24 24" aria-hidden="true"><path d="M12 3l10 9h-3v9h-5v-6h-4v6H5v-9H2z"/></svg>
        17C Tindale Ridge Rd.
      </li>
      <li class="contact__item">
        <span class="contact__icon" aria-hidden="true"></span>
        Kelvara NSW 2591
      </li>
    </ul>
  </section>
</main>
</body>
</html>
```